Coastline Premier Retreats Business Card Design

Design a business card for Coastline Premier Retreats. Look at the website for colors and reference. Card should have logo, name, title, office number, mobile number, email, URL and a tagline like, "Luxury Hotel & Resort Email Marketing" (This might change).

https://www.coastlinepremierretreats.example

The rest I will leave up to your imagination.

Contact Information for Business Card

Logo, name, title, office number, mobile number, email, URL and a tagline like, "Luxury Hotel & Resort Email Marketing" (This might change).

```html
<!DOCTYPE html>
<html lang="en">
<head>
<meta charset="utf-8">
<title>Coastline Premier Retreats – Business Card</title>
<link rel="stylesheet" href="https://fonts.googleapis.com/css2?family=Open+Sans:wght@400;600;700;800&display=swap">
<style>
  :root {
    --stage: #3a3a3a;
    --card: #1b1b1b;
    --orange: #f47a1f;
    --white: #f2f2f2;
    --muted: #d8d8d8;
  }
  * { box-sizing: border-box; margin: 0; padding: 0; }
  html, body { width: 1200px; height: 801px; overflow: hidden; }
  body {
    background: var(--stage);
    font-family: "Open Sans", Arial, sans-serif;
    position: relative;
  }
  .card {
    position: absolute;
    top: 252px;
    width: 520px;
    height: 297px;
    background: var(--card);
    border-bottom: 2px solid var(--orange);
    border-left: 1px solid var(--orange);
    box-shadow: 0 14px 30px rgba(0,0,0,.45);
    overflow: hidden;
  }
  .card--front { left: 50px; }
  .card--back { left: 630px; }

  .front-frame {
    position: absolute;
    inset: 24px;
    border: 3px solid var(--orange);
  }
  .tagline {
    position: absolute;
    right: 70px;
    bottom: -10px;
    padding: 0 10px;
    background: var(--card);
    color: var(--white);
    font-size: 12px;
    font-weight: 600;
    letter-spacing: .2px;
    line-height: 17px;
    white-space: nowrap;
  }
  .identity {
    position: absolute;
    left: 27px;
    right: 27px;
    top: 96px;
    display: flex;
    align-items: center;
    justify-content: center;
    white-space: nowrap;
  }
  .person { text-align: right; padding-right: 14px; }
  .person__name {
    color: var(--orange);
    font-size: 16px;
    font-weight: 800;
    letter-spacing: .3px;
    line-height: 1.15;
  }
  .person__title {
    color: var(--muted);
    font-size: 12px;
    font-weight: 400;
    margin-top: 2px;
  }
  .divider {
    width: 1px;
    height: 60px;
    background: var(--orange);
    flex: none;
  }
  .contacts { list-style: none; padding-left: 12px; }
  .contacts li {
    display: flex;
    align-items: center;
    gap: 6px;
    color: var(--white);
    font-size: 11px;
    line-height: 19px;
  }
  .contacts svg { width: 9px; height: 9px; fill: var(--orange); flex: none; }

  .brand {
    position: absolute;
    inset: 0;
    display: flex;
    align-items: center;
    justify-content: center;
    gap: 14px;
  }
  .brand__square { width: 18px; height: 18px; background: var(--orange); }
  .brand__name {
    color: var(--white);
    font-size: 27px;
    font-weight: 800;
    letter-spacing: .5px;
    text-transform: uppercase;
    line-height: 1.05;
  }
</style>
</head>
<body>
  <section class="card card--front" aria-label="Business card front">
    <div class="front-frame">
      <span class="tagline">Luxury Hotel &amp; Resort Email Marketing</span>
    </div>
    <div class="identity">
      <div class="person">
        <p class="person__name">DANIEL WHITMORE</p>
        <p class="person__title">President / CEO</p>
      </div>
      <div class="divider"></div>
      <ul class="contacts">
        <li>
          <svg viewBox="0 0 10 10" aria-hidden="true"><path d="M2 0.5l1.6 2-1 1.1a5.5 5.5 0 0 0 3.8 3.8l1.1-1 2 1.6-1 1.8C4 9.5 0.5 6 0.2 1.5z"/></svg>
          555.014.2700
        </li>
        <li>
          <svg viewBox="0 0 10 10" aria-hidden="true"><path d="M0 2h10v6H0z M0 2l5 3.5L10 2" stroke="#1b1b1b" stroke-width=".8"/></svg>
          info@coastlinepremierretreats.example
        </li>
        <li>
          <svg viewBox="0 0 10 10" aria-hidden="true"><circle cx="5" cy="5" r="5"/><path d="M0 5h10M5 0c-2 2.5-2 7.5 0 10M5 0c2 2.5 2 7.5 0 10" stroke="#1b1b1b" stroke-width=".8" fill="none"/></svg>
          www.coastlinepremierretreats.example
        </li>
      </ul>
    </div>
  </section>

  <section class="card card--back" aria-label="Business card back">
    <div class="brand">
      <span class="brand__square" aria-hidden="true"></span>
      <p class="brand__name">Coastline Premier<br>Retreats</p>
    </div>
  </section>
</body>
</html>
```